Ridgeline Journeys business card

please see website
www.ridgelinejourneys.comau

info needed on card
Curtis Halvey
Ph
email
Adventure Riding GPS trails

please use my logo and colours off my site

Curtis Halvey
curtis@ridgelinejourneys.com

```html
<!DOCTYPE html>
<html lang="en">
<head>
<meta charset="utf-8">
<title>Ridgeline Journeys – Business Card</title>
<link href="https://fonts.googleapis.com/css2?family=Open+Sans:ital,wght@0,400;0,700;0,800;1,700&display=swap" rel="stylesheet">
<style>
  :root{
    --bg:#8d8d8b;
    --card-black:#050505;
    --band-dark:#161616;
    --strip-white:#eeeeee;
    --yellow:#ffe11a;
    --yellow-deep:#f5c400;
    --text-white:#ffffff;
    --text-dark:#111111;
  }
  *{box-sizing:border-box;margin:0;padding:0}
  html,body{width:1200px;height:900px;overflow:hidden}
  body{background:var(--bg);font-family:"Open Sans",Arial,sans-serif;position:relative}

  .card{position:absolute;width:600px;height:343px;background:var(--card-black);overflow:hidden;
    box-shadow:0 10px 24px rgba(0,0,0,.35)}
  .card--back{left:360px;top:70px}
  .card--front{left:240px;top:480px}

  .brand{position:absolute;display:flex;align-items:center;gap:14px}
  .brand__square{width:34px;height:34px;background:var(--yellow);flex:none}
  .brand__name{font-weight:800;color:var(--text-white);text-transform:uppercase;line-height:1.02;letter-spacing:.5px;white-space:nowrap}

  .card--back .brand{left:220px;top:150px}
  .card--back .brand__name{font-size:38px}

  .strip{position:absolute;left:0;width:100%;height:12px;background:var(--strip-white)}
  .band{position:absolute;left:0;width:100%;background:linear-gradient(180deg,var(--yellow) 0%,var(--yellow-deep) 100%);
    display:flex;align-items:center;justify-content:center;color:var(--text-dark);white-space:nowrap}

  .card--back .strip{top:262px}
  .card--back .band{top:274px;height:69px;font-weight:700;font-size:16px}

  .person{position:absolute;right:40px;top:40px;color:var(--yellow);font-weight:700;font-size:20px;white-space:nowrap}
  .card--front .brand{left:40px;top:62px}
  .card--front .brand__name{font-size:30px}

  .contact{position:absolute;left:0;top:170px;width:100%;height:88px;background:var(--band-dark);
    display:flex;align-items:center;justify-content:space-between;padding:0 36px;color:var(--text-white);font-size:12px}
  .contact__item{display:flex;align-items:center;gap:7px;white-space:nowrap;flex:none}
  .contact__item svg{width:13px;height:13px;fill:var(--yellow);flex:none}

  .card--front .strip{top:258px}
  .card--front .band{top:270px;height:73px;font-weight:700;font-style:italic;font-size:17px}
</style>
</head>
<body>

<section class="card card--back" aria-label="Card back">
  <div class="brand">
    <span class="brand__square"></span>
    <span class="brand__name">Ridgeline<br>Journeys</span>
  </div>
  <div class="strip"></div>
  <div class="band">www.ridgelinejourneys.com</div>
</section>

<section class="card card--front" aria-label="Card front">
  <p class="person">Curtis Halvey</p>
  <div class="brand">
    <span class="brand__square"></span>
    <span class="brand__name">Ridgeline<br>Journeys</span>
  </div>
  <div class="contact">
    <span class="contact__item">
      <svg viewBox="0 0 24 24"><path d="M6.6 10.8a15.1 15.1 0 0 0 6.6 6.6l2.2-2.2a1 1 0 0 1 1-.25 11.4 11.4 0 0 0 3.6.57 1 1 0 0 1 1 1V20a1 1 0 0 1-1 1A17 17 0 0 1 3 4a1 1 0 0 1 1-1h3.5a1 1 0 0 1 1 1c0 1.250.2 2.450.57 3.570a1 1 0 0 1-.25 1z"/></svg>
      (044)-555-0142
    </span>
    <span class="contact__item">
      <svg viewBox="0 0 24 24"><path d="M2 5h20v14H2z M2 5l10 8 10-8" stroke="#161616" stroke-width="1.5"/></svg>
      info@ridgelinejourneys.com
    </span>
    <span class="contact__item">
      <svg viewBox="0 0 24 24"><path d="M10 14a4 4 0 0 1 0-5.7l3-3a4 4 0 0 1 5.7 5.7l-1.5 1.5-1.4-1.4 1.5-1.5a2 2 0 0 0-2.9-2.9l-3 3a2 2 0 0 0 0 2.9zM14 10a4 4 0 0 1 0 5.7l-3 3A4 4 0 0 1 5.3 13l1.5-1.5 1.4 1.4-1.5 1.5a2 2 0 0 0 2.9 2.9l3-3a2 2 0 0 0 0-2.9z"/></svg>
      www.ridgelinejourneys.com
    </span>
  </div>
  <div class="strip"></div>
  <div class="band">Adventure Riding GPS trails</div>
</section>

</body>
</html>
```